Steadfast Field Crews

We are a underground coal mining labour hire company, needing a website that links into our online payroll (www.wagelinkr.com.au) and also need to have job applications page that is a preform with drop down menu,s with answers or check boxes. We would also need a 3 tier administration access for access to different files.
We are looking for an ongoing relationship with future app integration

Reason: There are a few more designs to come and I'm out at the mine for another week

Industry/Entity Type

Coal Mining

```html
<!DOCTYPE html>
<html lang="en">
<head>
<meta charset="utf-8">
<title>Steadfast Field Crews</title>
<link href="https://fonts.googleapis.com/css2?family=Oswald:wght@400;500;600&family=Source+Sans+3:wght@400;600&display=swap" rel="stylesheet">
<style>
:root{
  --orange:#f26a21;
  --orange-light:#f7894a;
  --ink:#4a4a4a;
  --black:#000;
  --footer:#2d2d2d;
  --rule:#cfcfcf;
  --white:#fff;
}
*{margin:0;padding:0;box-sizing:border-box}
html,body{width:745px;height:1200px;overflow:hidden;background:var(--white)}
body{position:relative;font-family:"Source Sans 3",Arial,sans-serif;color:var(--ink)}
.abs{position:absolute}
.header{left:0;top:0;width:745px;height:97px;background:var(--black)}
.brand{left:72px;top:30px;display:flex;align-items:center;gap:7px;color:var(--orange);font-size:13px;font-weight:600;width:150px;line-height:1.15}
.brand-dot{width:22px;height:22px;border-radius:50%;background:var(--orange);flex:none}
.socials{display:flex;gap:5px}
.social{width:20px;height:20px;border:1.5px solid var(--white);border-radius:50%}
.socials-top{left:542px;top:21px}
.socials-foot{left:542px;top:1114px}
.call{left:385px;top:55px;display:flex;gap:8px;align-items:center;color:var(--white);font-family:"Oswald",sans-serif;font-size:11.5px;line-height:1.4}
.search{left:491px;top:54px;width:171px;height:27px;border:1px solid #bbb;color:var(--white);font-size:8px;padding:8px 0 0 9px}
.search svg{position:absolute;right:10px;top:6px}
.nav{left:82px;top:99px;width:581px;height:31px;background:linear-gradient(var(--orange-light),var(--orange));display:flex;justify-content:space-around;align-items:center;padding:0 14px}
.nav a{color:var(--white);font-size:8.5px;text-decoration:none}
.slider{left:82px;top:133px;width:581px;height:275px;background:linear-gradient(110deg,#555,#1a1a1a 40%,#6a6a6a 70%,#222)}
.caption{left:134px;top:228px;width:285px;height:86px;background:rgba(220,220,220,.85);padding:7px 0 0 21px;font-family:"Oswald",sans-serif;font-weight:500;font-size:26px;line-height:40px;color:var(--orange);letter-spacing:.5px}
.arrow{top:239px;width:23px;height:64px;background:var(--white);display:flex;align-items:center;justify-content:center}
h2{font-weight:400;font-size:12.5px;color:var(--orange)}
.copy{font-size:7px;line-height:17.6px}
.col-copy{font-size:7px;line-height:15.7px;width:180px}
.photo{background:linear-gradient(135deg,#3a3026,#8a6a3a 50%,#1d1a16)}
.btn{width:67px;height:25px;background:var(--orange);color:var(--white);font-size:8.5px;display:flex;align-items:center;justify-content:center}
.news-item{left:82px;width:186px;height:56px;border-bottom:1px solid var(--rule);display:flex;gap:16px;align-items:flex-start}
.date{width:40px;height:40px;margin-top:4px;border-radius:50%;background:var(--orange);color:var(--white);font-family:"Oswald",sans-serif;font-size:12px;line-height:14px;text-align:center;padding-top:6px;flex:none}
.news-text{font-size:6.6px;line-height:15.7px;color:#222;width:130px}
.services{left:289px;top:900px;list-style:none;font-size:7px;color:#222}
.services li{height:20.4px;display:flex;gap:8px;align-items:center}
.quote{left:482px;top:896px;width:180px;font-size:7px;line-height:15.7px;padding-left:10px}
.mark{font-family:Georgia,serif;font-size:16px;color:#444;line-height:1}
.footer{left:0;top:1096px;width:745px;height:104px;background:var(--footer)}
.fnav{left:83px;top:1123px;display:flex;gap:12px;font-size:7.5px;color:var(--white)}
</style>
</head>
<body>
<div class="abs header"></div>
<div class="abs brand"><span class="brand-dot"></span><span>Steadfast Field Crews</span></div>
<div class="abs socials socials-top"><span class="social"></span><span class="social"></span><span class="social"></span><span class="social"></span><span class="social"></span></div>
<div class="abs call">
  <svg width="21" height="21" viewBox="0 0 21 21"><circle cx="10.5" cy="10.5" r="9.5" fill="none" stroke="#f26a21" stroke-width="1.5"/><path d="M7 6c-1 1-1 3 1 5.5S13 15 14.5 14l.5-1.2-2-1.3-1 .8c-1-.5-2.5-2-3-3l.8-1-1.3-2z" fill="#f26a21"/></svg>
  <div>Call Us Today<br>800417259</div>
</div>
<div class="abs search">Search<svg width="14" height="14" viewBox="0 0 14 14"><circle cx="5.5" cy="5.5" r="4" fill="none" stroke="#fff" stroke-width="1.5"/><path d="M8.5 8.5l4 4" stroke="#fff" stroke-width="2"/></svg></div>

<nav class="abs nav"><a>Home</a><a>Apply for position</a><a>Pay Portal</a><a>Download</a><a>Mission</a><a>About us</a><a>Contact us</a></nav>

<div class="abs slider" role="img" aria-label="Black and white photo of two coal miners with headlamps in a timbered tunnel"></div>
<div class="abs caption">The underground coal<br>miner company.</div>
<div class="abs arrow" style="left:82px"><svg width="10" height="18"><path d="M9 1L1 9l8 8" fill="none" stroke="#333" stroke-width="1.5"/></svg></div>
<div class="abs arrow" style="left:641px"><svg width="10" height="18"><path d="M1 1l8 8-8 8" fill="none" stroke="#333" stroke-width="1.5"/></svg></div>

<h2 class="abs" style="left:82px;top:418px">Welcome to Our Company</h2>
<p class="abs copy" style="left:82px;top:449px;width:380px">We are KTRW pty ltd trading as Steadfast Field Crews, we are experienced inground consolidation in underground coal mines, in short when they collapse or cave inwe come in with chemical pumps and stabilise the ground or fill cavities which will thenallow for the mining process to continue. We also do general mine labor as well.</p>
<p class="abs copy" style="left:82px;top:513px;width:380px">We are a labor hire company for major mining services company, we offer labor solutionsin New South Wales and Queensland in the underground coal mines.........</p>
<div class="abs photo" style="left:481px;top:427px;width:181px;height:131px;background:linear-gradient(135deg,#2a2a2a,#777 50%,#1e1e1e)" role="img" aria-label="Longwall shearer machine in an underground coal seam"></div>

<div class="abs photo" style="left:82px;top:581px;width:181px;height:117px" role="img" aria-label="Miner operating heavy drilling equipment underground"></div>
<div class="abs photo" style="left:282px;top:581px;width:181px;height:117px;background:linear-gradient(135deg,#2a2520,#c07a30 55%,#3a2e22)" role="img" aria-label="Miner in orange hi-vis and hard hat working with tools"></div>
<div class="abs photo" style="left:481px;top:581px;width:181px;height:117px;background:linear-gradient(135deg,#1e1a22,#a0502a 50%,#2a2020)" role="img" aria-label="Crew in hi-vis gear working underground"></div>

<h2 class="abs" style="left:82px;top:709px">Underground</h2>
<h2 class="abs" style="left:282px;top:709px">Services</h2>
<h2 class="abs" style="left:481px;top:709px">Engineering</h2>
<p class="abs col-copy" style="left:82px;top:730px">Coalridge Group Ltd is a specialist provider of mining services to the Australian coal mining industry. The Company is a market leader providing an extensive range of outsourced services to existing and new coal mining operations........</p>
<p class="abs col-copy" style="left:282px;top:730px">Coalridge Group Ltd is a specialist provider of mining services to the Australian coal mining industry. The Company is a market leader providing an extensive range of outsourced services to existing and new coal mining operations........</p>
<p class="abs col-copy" style="left:481px;top:730px">Coalridge Group Ltd is a specialist provider of mining services to the Australian coal mining industry. The Company is a market leader providing an extensive range of outsourced services to existing and new coal mining operations........</p>
<div class="abs btn" style="left:82px;top:821px">Read More</div>
<div class="abs btn" style="left:282px;top:821px">Read More</div>
<div class="abs btn" style="left:481px;top:821px">Read More</div>

<h2 class="abs" style="left:82px;top:870px">News &amp; Event</h2>
<h2 class="abs" style="left:289px;top:870px">Our Services</h2>
<h2 class="abs" style="left:482px;top:870px">Testimonials</h2>

<div class="abs news-item" style="top:899px"><div class="date">19<br>Jan</div><p class="news-text">Latin professor at Ashvale College in Norfield, looked up one of the more obscure passage.......</p></div>
<div class="abs news-item" style="top:959px"><div class="date">19<br>Jan</div><p class="news-text">Latin professor at Ashvale College in Norfield, looked up one of the more obscure passage.......</p></div>
<div class="abs news-item" style="top:1019px"><div class="date">19<br>Jan</div><p class="news-text" style="color:#999">Latin professor at Ashvale College in Norfield, looked up one of the more obscure passage.......</p></div>

<ul class="abs services">
  <li><svg width="8" height="7"><path d="M1 4l2 2 4-5" fill="none" stroke="#f26a21" stroke-width="1.3"/></svg>Underground roadway development</li>
  <li><svg width="8" height="7"><path d="M1 4l2 2 4-5" fill="none" stroke="#f26a21" stroke-width="1.3"/></svg>Installation of conveyors</li>
  <li><svg width="8" height="7"><path d="M1 4l2 2 4-5" fill="none" stroke="#f26a21" stroke-width="1.3"/></svg>Longwall relocation and maintenance</li>
  <li><svg width="8" height="7"><path d="M1 4l2 2 4-5" fill="none" stroke="#f26a21" stroke-width="1.3"/></svg>Supply and installation of ventilation control devices</li>
  <li><svg width="8" height="7"><path d="M1 4l2 2 4-5" fill="none" stroke="#f26a21" stroke-width="1.3"/></svg>Installation of secondary support</li>
  <li><svg width="8" height="7"><path d="M1 4l2 2 4-5" fill="none" stroke="#f26a21" stroke-width="1.3"/></svg>Equipment hire</li>
  <li><svg width="8" height="7"><path d="M1 4l2 2 4-5" fill="none" stroke="#f26a21" stroke-width="1.3"/></svg>In-seam directional drilling</li>
</ul>
<div class="abs btn" style="left:290px;top:1049px">Learn More</div>

<span class="abs mark" style="left:474px;top:896px">&ldquo;</span>
<p class="abs quote">Coalridge Group Ltd is a specialist provider of mining services to the Australian coal mining industry. The Company is a market leader providing an extensive range of outsourced services to existing and new coal mining operations. Coalridge also has a comprehensive range of underground mining equipment which complements its contracting operations.. .... <span class="mark">&rdquo;</span></p>
<p class="abs" style="left:560px;top:1036px;width:100px;text-align:right;color:var(--orange);font-size:11px">Daniel Brooke</p>
<p class="abs" style="left:560px;top:1051px;width:102px;text-align:right;font-size:7px;color:#222">22 Jan 2014</p>

<div class="abs footer"></div>
<div class="abs fnav"><span>Home</span><span>/</span><span>Apply for position</span><span>/</span><span>Pay Portal</span><span>/</span><span>Download</span><span>/</span><span>Mission</span><span>/</span><span>About us</span><span>/</span><span>Contact us</span></div>
<div class="abs socials socials-foot"><span class="social"></span><span class="social"></span><span class="social"></span><span class="social"></span><span class="social"></span></div>
<p class="abs" style="left:82px;top:1157px;font-size:7.2px;color:var(--white)">Copyright 2014 Underground Coal Mine.All Right Reseved.</p>
<p class="abs" style="left:520px;top:1146px;width:142px;text-align:right;font-size:28px;color:var(--white)">wagelinkr</p>
</body>
</html>
```